Company Flyer for Electric boating company

I am looking for a company flyer which we can hand over to boat owners in the Netherlands (Amsterdam area). Our core business is to rebuild every boat (from 4 to 10 meters) into an electrically propelled boat. We are taking out diesels and replace them with a high quality electrical motor, inboard varying from 30 till 80 pk (hp). And outboard from 1pk (hp) till 200pk. We are the best, not the cheapest, not the most expensive. We only work with the best materials. The flyer has to be sort of in line with our website and branding.

Major advantages of electric boating are:
- completely silent
- no fumes, smells or smoke
- cheap to operate
- environmentally friendly
- obliged in more and more areas
- no maintenance
- more enjoyable

The flyer should be A5 format. Since all the text has to be in Dutch I expect only the graphical design and layout for advantages, process, pricing and contact details etc.

Target Market(s)

Boat owners in the Netherlands

Font styles to use
Sans Serif

Colors
9bcb3c
add136
cadf82
0555a3
3176b5
85acd3
e0ebf3

Requirements
Must have
• Clean design, in line with website: www.volthaven.nl
Nice to have
• icons for advantages, boating etc

2 sides
Should not have
• Steering wheel...

```html
<!DOCTYPE html>
<html lang="nl">
<head>
<meta charset="utf-8">
<title>Volthaven – flyer ontwerpen</title>
<link href="https://fonts.googleapis.com/css2?family=Barlow+Condensed:wght@700&family=Roboto:wght@400;700&display=swap" rel="stylesheet">
<style>
:root{
  --board:#e6e6e6;
  --ink:#111314;
  --dark:#1b1e20;
  --white:#ffffff;
  --green:#9bcb3c;
  --lime:#add136;
  --pale:#cadf82;
  --grey:#8a8f93;
  --light:#f2f3f3;
  --photo-dark:linear-gradient(160deg,#3a4147,#15181b 70%);
  --photo-water:linear-gradient(170deg,#9fb1bd,#4f6470 60%,#2c353b);
  --photo-boat:linear-gradient(160deg,#c7cdd1,#7b868d 55%,#3b4247);
}
*{box-sizing:border-box;margin:0;padding:0}
html,body{width:861px;height:1200px;overflow:hidden;background:var(--board);font-family:"Roboto",Arial,sans-serif;color:var(--ink)}
.board{position:relative;width:861px;height:1200px}
.page{position:absolute;width:218px;height:290px;background:var(--white);overflow:hidden;box-shadow:0 2px 6px rgba(0,0,0,.18)}
.label{position:absolute;font-size:6px;letter-spacing:.5px;color:var(--grey)}
.abs{position:absolute}
.photo{position:absolute}
.dark{background:var(--photo-dark)}
.water{background:var(--photo-water)}
.boat{background:var(--photo-boat)}
.black{background:var(--ink)}
.brand{position:absolute;display:flex;align-items:center;gap:3px;font-weight:700;font-size:7px;color:var(--white);letter-spacing:.4px}
.brand i{width:7px;height:7px;border-radius:50%;background:var(--green);display:block}
.headline{position:absolute;font-family:"Barlow Condensed",Arial,sans-serif;font-weight:700;line-height:.95;text-transform:uppercase}
.sub{position:absolute;font-size:5px;color:var(--green);font-weight:700}
.tiny{font-size:3.2px;line-height:4.4px;color:#555}
.tiny.light{color:#c9cccf}
.col-title{font-size:4.4px;font-weight:700;margin-bottom:2px}
.price{font-family:"Barlow Condensed",Arial,sans-serif;font-weight:700;font-size:9px;color:var(--green)}
.cols{position:absolute;display:flex;gap:5px}
.cols>div{flex:1}
.footer{position:absolute;left:0;bottom:0;width:100%;height:14px;background:var(--ink);display:flex;align-items:center;justify-content:space-around;font-size:3.6px;color:var(--white)}
.footer span{display:flex;align-items:center;gap:2px}
.footer svg{width:5px;height:5px}
.rule{position:absolute;height:2px;background:var(--green)}
.gbox{background:var(--green);color:var(--white);padding:4px 3px;height:36px}
.gbox .price{color:var(--white)}
.panel-title{font-size:5px;font-weight:700;color:var(--green);margin-bottom:3px}
.check{display:flex;gap:2px;align-items:flex-start;margin-bottom:3px}
.check svg{width:4px;height:4px;flex:none;margin-top:.3px}
</style>
</head>
<body>
<div class="board">

<!-- Row 1 front -->
<section class="page" style="left:207px;top:100px">
  <div class="photo dark" style="left:0;top:0;width:218px;height:150px" role="img" aria-label="Donkere foto van een boot in aanbouw in de werkplaats"></div>
  <div class="brand" style="left:10px;top:9px"><i></i>VOLTHAVEN</div>
  <h1 class="headline" style="left:10px;top:56px;font-size:21px;color:var(--white)">Boat Rebuilding</h1>
  <p class="sub" style="left:10px;top:78px">Van diesel naar stil elektrisch varen</p>
  <div class="abs" style="left:10px;top:160px;font-size:5px;font-weight:700">Uw boot elektrisch, van 4 tot 10 meter</div>
  <div class="cols" style="left:10px;top:172px;width:198px">
    <div><div class="price">30 pk</div><p class="tiny">Inboard motor, stil en krachtig voor sloep.</p></div>
    <div><div class="price">50 pk</div><p class="tiny">Inboard motor voor grotere boten tot tien meter.</p></div>
    <div><div class="price">80 pk</div><p class="tiny">Zwaarste inboard, volledig geplaatst en getest.</p></div>
    <div><div class="price">200 pk</div><p class="tiny">Outboard vanaf 1 pk tot 200 pk leverbaar.</p></div>
  </div>
  <div class="rule" style="left:10px;top:222px;width:198px"></div>
  <div class="abs" style="left:10px;top:230px;width:198px;text-align:center;font-size:4.4px;font-weight:700">Vraag vandaag nog een vrijblijvende offerte aan</div>
  <p class="abs tiny" style="left:30px;top:240px;width:158px;text-align:center">Wij zijn niet de goedkoopste, niet de duurste, maar de beste.</p>
  <div class="footer">
    <span><svg viewBox="0 0 10 10"><path d="M2 1h2l1 3-1.5 1a6 6 0 0 0 2.5 2.5L7 6l3 1v2a1 1 0 0 1-1 1A8 8 0 0 1 1 2a1 1 0 0 1 1-1z" fill="#9bcb3c"/></svg>020 555 0199</span>
    <span><svg viewBox="0 0 10 10"><rect x="1" y="2" width="8" height="6" fill="none" stroke="#9bcb3c"/><path d="M1 2l4 3 4-3" fill="none" stroke="#9bcb3c"/></svg>info@volthaven.nl</span>
    <span><svg viewBox="0 0 10 10"><circle cx="5" cy="5" r="4" fill="none" stroke="#9bcb3c"/></svg>www.volthaven.nl</span>
  </div>
</section>
<div class="label" style="left:207px;top:392px">FRONT</div>

<!-- Row 1 back -->
<section class="page" style="left:436px;top:100px">
  <div class="abs black" style="left:0;top:0;width:100px;height:14px"></div>
  <div class="abs" style="left:6px;top:4px;font-size:4.4px;color:var(--white);font-weight:700">Waarom elektrisch varen?</div>
  <div class="photo dark" style="left:104px;top:0;width:114px;height:70px" role="img" aria-label="Foto van een donkere motorboot op het water"></div>
  <div class="abs" style="left:6px;top:22px;width:90px">
    <div class="check"><svg viewBox="0 0 10 10"><path d="M1 5l3 3 5-6" stroke="#9bcb3c" stroke-width="2" fill="none"/></svg><p class="tiny">Volledig stil varen op elk water.</p></div>
    <div class="check"><svg viewBox="0 0 10 10"><path d="M1 5l3 3 5-6" stroke="#9bcb3c" stroke-width="2" fill="none"/></svg><p class="tiny">Geen uitlaatgassen, geur of rook.</p></div>
    <div class="check"><svg viewBox="0 0 10 10"><path d="M1 5l3 3 5-6" stroke="#9bcb3c" stroke-width="2" fill="none"/></svg><p class="tiny">Goedkoop in gebruik en onderhoud.</p></div>
    <div class="check"><svg viewBox="0 0 10 10"><path d="M1 5l3 3 5-6" stroke="#9bcb3c" stroke-width="2" fill="none"/></svg><p class="tiny">Beter voor het milieu.</p></div>
    <div class="check"><svg viewBox="0 0 10 10"><path d="M1 5l3 3 5-6" stroke="#9bcb3c" stroke-width="2" fill="none"/></svg><p class="tiny">Steeds vaker verplicht in de stad.</p></div>
    <div class="check"><svg viewBox="0 0 10 10"><path d="M1 5l3 3 5-6" stroke="#9bcb3c" stroke-width="2" fill="none"/></svg><p class="tiny">Meer plezier aan boord.</p></div>
  </div>
  <div class="abs" style="left:6px;top:120px;width:90px">
    <div class="col-title">Ons proces</div>
    <p class="tiny">Wij halen de diesel eruit en plaatsen een hoogwaardige elektromotor met accu en lader.</p>
  </div>
  <div class="abs" style="left:6px;top:170px;width:90px">
    <div class="col-title">Kwaliteit</div>
    <p class="tiny">Wij werken alleen met de beste materialen en vakmensen.</p>
  </div>
  <div class="photo boat" style="left:104px;top:74px;width:114px;height:58px" role="img" aria-label="Foto van een sloep aan de kade"></div>
  <div class="photo water" style="left:104px;top:136px;width:114px;height:60px" role="img" aria-label="Foto van een oranje reddingsboot in de werkplaats"></div>
  <div class="photo dark" style="left:104px;top:200px;width:114px;height:90px" role="img" aria-label="Foto van een romp in de werkplaats"></div>
</section>
<div class="label" style="left:436px;top:392px">BACK</div>

<!-- Row 2 front -->
<section class="page" style="left:207px;top:460px">
  <div class="abs black" style="left:0;top:0;width:109px;height:128px"></div>
  <div class="photo water" style="left:109px;top:0;width:109px;height:128px" role="img" aria-label="Foto van een boeg die door het water snijdt"></div>
  <div class="brand" style="left:9px;top:9px"><i></i>VOLTHAVEN</div>
  <h1 class="headline" style="left:9px;top:40px;font-size:19px;color:var(--green)">Boating<br><span style="color:var(--white)">Company</span></h1>
  <p class="sub" style="left:9px;top:82px;width:92px;color:var(--white);font-weight:400">Wij bouwen uw boot om naar <b style="color:var(--green)">elektrisch</b></p>
  <div class="cols" style="left:9px;top:138px;width:200px">
    <div><div class="price">30 pk</div><p class="tiny">Stille inboard motor voor sloep.</p></div>
    <div><div class="price">50 pk</div><p class="tiny">Krachtige inboard tot tien meter.</p></div>
    <div><div class="price">80 pk</div><p class="tiny">Zwaarste inboard, volledig getest.</p></div>
    <div><div class="price">200 pk</div><p class="tiny">Outboard van 1 tot 200 pk.</p></div>
  </div>
  <div class="rule" style="left:9px;top:176px;width:200px"></div>
  <div class="photo boat" style="left:9px;top:184px;width:98px;height:84px" role="img" aria-label="Foto van een elektrische motor in een boot"></div>
  <div class="abs" style="left:113px;top:186px;width:96px">
    <div class="col-title">Waarom elektrisch?</div>
    <p class="tiny">Stil, schoon, goedkoop en zonder onderhoud. Steeds vaker verplicht in Amsterdam.</p>
  </div>
  <div class="footer">
    <span>020 555 0199</span><span>info@volthaven.nl</span><span>www.volthaven.nl</span>
  </div>
</section>
<div class="label" style="left:207px;top:752px">FRONT</div>

<!-- Row 2 back -->
<section class="page" style="left:436px;top:460px">
  <div class="photo boat" style="left:0;top:0;width:109px;height:60px" role="img" aria-label="Foto van een boot in de hal"></div>
  <div class="abs" style="left:6px;top:68px;width:98px">
    <div class="col-title">Ons proces</div>
    <div class="check"><svg viewBox="0 0 10 10"><circle cx="5" cy="5" r="4" fill="#9bcb3c"/></svg><p class="tiny">Kennismaking en advies aan boord.</p></div>
    <div class="check"><svg viewBox="0 0 10 10"><circle cx="5" cy="5" r="4" fill="#9bcb3c"/></svg><p class="tiny">Offerte op maat binnen een week.</p></div>
    <div class="check"><svg viewBox="0 0 10 10"><circle cx="5" cy="5" r="4" fill="#9bcb3c"/></svg><p class="tiny">Ombouw in onze eigen werf.</p></div>
    <div class="check"><svg viewBox="0 0 10 10"><circle cx="5" cy="5" r="4" fill="#9bcb3c"/></svg><p class="tiny">Proefvaart en oplevering.</p></div>
  </div>
  <div class="abs black" style="left:113px;top:0;width:105px;height:128px"></div>
  <div class="abs" style="left:119px;top:10px;width:93px">
    <div class="panel-title">Elektrisch varen</div>
    <p class="tiny light">Volledig stil, geen geur of rook en goedkoop in gebruik. Meer plezier op het water.</p>
  </div>
  <svg class="abs" style="left:150px;top:80px" width="28" height="28" viewBox="0 0 28 28"><circle cx="14" cy="14" r="12" fill="none" stroke="#9bcb3c" stroke-width="2"/><path d="M15 5l-6 10h5l-2 8 7-11h-5z" fill="#9bcb3c"/></svg>
  <div class="photo water" style="left:0;top:140px;width:72px;height:70px" role="img" aria-label="Foto van boten in de haven"></div>
  <div class="photo dark" style="left:73px;top:140px;width:72px;height:70px" role="img" aria-label="Foto van een motorruimte"></div>
  <div class="photo boat" style="left:146px;top:140px;width:72px;height:70px" role="img" aria-label="Foto van een sloep op de gracht"></div>
  <div class="photo boat" style="left:0;top:211px;width:72px;height:79px" role="img" aria-label="Foto van een romp op de kant"></div>
  <div class="photo water" style="left:73px;top:211px;width:72px;height:79px" role="img" aria-label="Foto van een varende boot"></div>
  <div class="photo dark" style="left:146px;top:211px;width:72px;height:79px" role="img" aria-label="Foto van een boot in de werkplaats"></div>
</section>
<div class="label" style="left:436px;top:752px">BACK</div>

<!-- Row 3 front -->
<section class="page" style="left:207px;top:832px">
  <div class="abs black" style="left:0;top:0;width:109px;height:128px"></div>
  <div class="photo water" style="left:109px;top:0;width:109px;height:128px" role="img" aria-label="Foto van een boeg die door het water snijdt"></div>
  <div class="brand" style="left:9px;top:9px"><i></i>VOLTHAVEN</div>
  <h1 class="headline" style="left:9px;top:40px;font-size:19px;color:var(--green)">Boating<br><span style="color:var(--white)">Company</span></h1>
  <p class="sub" style="left:9px;top:82px;width:92px;color:var(--white);font-weight:400">Wij bouwen uw boot om naar <b style="color:var(--green)">elektrisch</b></p>
  <div class="cols" style="left:9px;top:136px;width:200px;gap:4px">
    <div class="gbox"><div class="price">30 pk</div><p class="tiny" style="color:#fff">Stille inboard.</p></div>
    <div class="gbox"><div class="price">50 pk</div><p class="tiny" style="color:#fff">Tot tien meter.</p></div>
    <div class="gbox"><div class="price">80 pk</div><p class="tiny" style="color:#fff">Zwaarste inboard.</p></div>
    <div class="gbox"><div class="price">200 pk</div><p class="tiny" style="color:#fff">Outboard leverbaar.</p></div>
  </div>
  <div class="photo boat" style="left:9px;top:184px;width:98px;height:84px" role="img" aria-label="Foto van een elektrische motor in een boot"></div>
  <div class="abs" style="left:113px;top:186px;width:96px">
    <div class="col-title">Waarom elektrisch?</div>
    <p class="tiny">Stil, schoon, goedkoop en zonder onderhoud. Steeds vaker verplicht in Amsterdam.</p>
  </div>
  <div class="footer">
    <span>020 555 0199</span><span>info@volthaven.nl</span><span>www.volthaven.nl</span>
  </div>
</section>
<div class="label" style="left:207px;top:1118px">FRONT</div>

<!-- Row 3 back -->
<section class="page" style="left:436px;top:832px">
  <div class="photo boat" style="left:0;top:0;width:109px;height:60px" role="img" aria-label="Foto van een boot in de hal"></div>
  <div class="abs" style="left:6px;top:68px;width:98px">
    <div class="col-title">Ons proces</div>
    <div class="check"><svg viewBox="0 0 10 10"><circle cx="5" cy="5" r="4" fill="#9bcb3c"/></svg><p class="tiny">Kennismaking en advies aan boord.</p></div>
    <div class="check"><svg viewBox="0 0 10 10"><circle cx="5" cy="5" r="4" fill="#9bcb3c"/></svg><p class="tiny">Offerte op maat binnen een week.</p></div>
    <div class="check"><svg viewBox="0 0 10 10"><circle cx="5" cy="5" r="4" fill="#9bcb3c"/></svg><p class="tiny">Ombouw in onze eigen werf.</p></div>
  </div>
  <div class="abs" style="left:113px;top:0;width:105px;height:128px;background:var(--green)"></div>
  <div class="abs" style="left:119px;top:10px;width:93px">
    <div class="panel-title" style="color:var(--white)">Elektrisch varen</div>
    <p class="tiny" style="color:var(--white)">Volledig stil, geen geur of rook en goedkoop in gebruik. Meer plezier op het water.</p>
  </div>
  <svg class="abs" style="left:150px;top:80px" width="28" height="28" viewBox="0 0 28 28"><circle cx="14" cy="14" r="12" fill="none" stroke="#111314" stroke-width="2"/><path d="M15 5l-6 10h5l-2 8 7-11h-5z" fill="#111314"/></svg>
  <div class="photo water" style="left:0;top:140px;width:72px;height:70px" role="img" aria-label="Foto van boten in de haven"></div>
  <div class="photo dark" style="left:73px;top:140px;width:72px;height:70px" role="img" aria-label="Foto van een motorruimte"></div>
  <div class="photo boat" style="left:146px;top:140px;width:72px;height:70px" role="img" aria-label="Foto van een sloep op de gracht"></div>
  <div class="photo boat" style="left:0;top:211px;width:72px;height:79px" role="img" aria-label="Foto van een romp op de kant"></div>
  <div class="photo water" style="left:73px;top:211px;width:72px;height:79px" role="img" aria-label="Foto van een varende boot"></div>
  <div class="photo dark" style="left:146px;top:211px;width:72px;height:79px" role="img" aria-label="Foto van een boot in de werkplaats"></div>
</section>
<div class="label" style="left:436px;top:1118px">BACK</div>

</div>
</body>
</html>
```